Breakfast Cafe - The Sunny Nook

It is for my breakfast and lunch cafe with a hawaiian / beach theme. I am open 7 days a week from 7am to 2pm. We serve traditional American food such as omelettes, pancakes, burgers and sandwiches. I'll upload my old card and my new logo to be used. We have a lot of day to day regulars who eat there during the week, our t-shirts actually say 'Locals Only' on them. Hope this helps. Thanks.

Target Market(s)

anyone who has an appetite!

Industry/Entity Type

American Restaurant

Contact Information for Business Card

4815C Marlow Grove Avenue
Long Beach, California
(555) 731-2294

Requirements
Must have
• Address and phone number easily readable.
Nice to have
• beach or tropical theme

```html
<!DOCTYPE html>
<html lang="en">
<head>
<meta charset="utf-8">
<title>The Sunny Nook — Business Card</title>
<link href="https://fonts.googleapis.com/css2?family=Bebas+Neue&family=Yellowtail&display=swap" rel="stylesheet">
<style>
  :root {
    --backdrop: #1e1e1e;
    --card-paper: #f3ebdd;
    --edge-brown: #5a4a3a;
    --rust: #b5600f;
    --sky: #4fb9d6;
    --crimson: #c8102e;
    --logo-disc: #e9a13b;
  }
  html, body {
    margin: 0;
    padding: 0;
    width: 1200px;
    height: 960px;
    overflow: hidden;
    background: var(--backdrop);
  }
  .business-card {
    position: absolute;
    left: 300px;
    top: 308px;
    width: 600px;
    height: 344px;
    border-radius: 18px;
    background: var(--card-paper);
    overflow: hidden;
    font-family: "Bebas Neue", "Arial Narrow", sans-serif;
  }
  .card-edge {
    position: absolute;
    inset: 0;
    border-radius: 18px;
    box-shadow: inset 0 0 34px 14px rgba(90, 74, 58, 0.85);
  }
  .brand-block {
    position: absolute;
    left: 60px;
    top: 60px;
    width: 228px;
    text-align: center;
  }
  .brand-disc {
    display: block;
    margin: 0 auto;
  }
  .brand-name {
    margin: 8px 0 0;
    font-size: 40px;
    line-height: 1;
    color: var(--sky);
    letter-spacing: 1px;
    font-weight: 400;
  }
  .contact-block {
    position: absolute;
    left: 310px;
    top: 68px;
    width: 270px;
  }
  .contact-block p { margin: 0; }
  .address {
    font-size: 24px;
    line-height: 22px;
    color: var(--rust);
  }
  .phone {
    margin-top: 4px !important;
    font-size: 29px;
    line-height: 30px;
    color: var(--sky);
  }
  .cafe-type {
    margin-top: 10px !important;
    font-size: 25px;
    line-height: 24px;
    color: var(--rust);
  }
  .hours {
    font-size: 19px;
    line-height: 21px;
    color: var(--sky);
  }
  .menu-note {
    font-size: 15px;
    line-height: 18px;
    color: var(--crimson);
  }
  .tagline {
    margin-top: 6px !important;
    font-family: "Yellowtail", cursive;
    font-size: 40px;
    line-height: 48px;
    color: var(--rust);
  }
</style>
</head>
<body>
  <article class="business-card">
    <div class="card-edge" role="img" aria-label="Weathered brown brushed border around the card"></div>

    <div class="brand-block">
      <svg class="brand-disc" width="150" height="150" viewBox="0 0 150 150" aria-hidden="true">
        <circle cx="75" cy="75" r="72" fill="var(--logo-disc)"/>
      </svg>
      <h1 class="brand-name">The Sunny Nook</h1>
    </div>

    <div class="contact-block">
      <p class="address">4815C Marlow Grove Avenue<br>Long Beach, California</p>
      <p class="phone">P.(555) 731-2294</p>
      <p class="cafe-type">Breakfast &amp; Lunch Cafe</p>
      <p class="hours">Open 7 days a week from 7am to 2pm.</p>
      <p class="menu-note">Serving traditional American food</p>
      <p class="tagline">Locals Only</p>
    </div>
  </article>
</body>
</html>
```